uk based ecommerce website requires fresh look ,high quality look and feel

we are a web based company selling eco friendly ground reinforcement grids to diy and construction sectors
our existing website is www.pondermeshpaths.co.uk ,

we have already updated the logo so that is the branding sorted .so we need a ecommerce website that is very much up-to date in design and layout and which has content management system for ease of use so that we can add products and information as required.

Use current logo as reference for colour scheme.
www.pondermeshpaths.co.uk

The current website has 6 pages accessible through the navigation bar, I would now like 5 pages, removing the need for the Trade Enquiries page possibly have it with along with contact us.

Target Market(s)

construction industry , diy end users,
retail market, landscapers, gardeners

Industry/Entity Type

Construction

Font styles to use
Other font styles liked:
• logo font prometo

Colors
f78f20
9bcb3c

Requirements
Must have
• logo colours and logo design in website with cms responsive design for tablet and mobile devices
• expect content to work flawlessly and look great across all devices
• HTML 5 custom design with coding as required
• must have good experiance in ecommerce website design
• eye catching, high quality look and feel and very user friedly ,very up-to date.
Nice to have
• picture slider show
• explain in writing what exactly i am getting in my ecommerce website
Should not have
• plain , basic design , old fashion looking ,cheap look

```html
<!DOCTYPE html>
<html lang="en">
<head>
<meta charset="utf-8">
<title>Pondermesh Driveways</title>
<link href="https://fonts.googleapis.com/css2?family=Open+Sans:wght@400;600;700;800&display=swap" rel="stylesheet">
<style>
:root{
  --orange:#f78f20;
  --orange-dark:#e86f0c;
  --green:#9bcb3c;
  --green-dark:#78a824;
  --ink:#333333;
  --muted:#666666;
  --light:#f3f3f3;
  --line:#e2e2e2;
  --footer:#3a3a3a;
  --white:#ffffff;
}
*{box-sizing:border-box;margin:0;padding:0}
html,body{width:1200px;height:2913px;overflow:hidden}
body{font-family:"Open Sans",Arial,sans-serif;color:var(--ink);background:var(--white);position:relative}
.abs{position:absolute}
section,header,nav,footer{position:absolute;left:0;width:1200px}

/* header */
.site-header{top:0;height:107px;background:var(--white)}
.brand{left:87px;top:22px;display:flex;align-items:center;gap:12px}
.brand-dot{width:52px;height:52px;border-radius:50%;background:var(--green)}
.brand-name{font-weight:800;font-size:24px;color:var(--orange);letter-spacing:.5px}
.contact-chip{top:26px;display:flex;align-items:center;gap:18px}
.chip-icon{width:50px;height:50px;border-radius:50%;background:var(--green);display:flex;align-items:center;justify-content:center}
.chip-label{font-size:17px;color:var(--ink);line-height:1.35}
.chip-label b{font-weight:400;display:block}

/* nav */
.main-nav{top:107px;height:56px;background:linear-gradient(#fba13c,var(--orange-dark));border-bottom:3px solid #f0c79a}
.nav-item{top:0;height:53px;line-height:53px;font-size:13px;font-weight:600;color:var(--white)}
.nav-item.active{left:87px;width:113px;text-align:center;background:var(--green)}
.search{left:899px;top:9px;width:214px;height:36px;background:var(--white);border-radius:2px;font-size:13px;color:#888;padding:0 14px;line-height:36px}
.search svg{position:absolute;right:12px;top:11px}

/* hero */
.hero{top:166px;height:471px;background:linear-gradient(115deg,#5a5a5a,#3c3c3c 55%,#2f2f2f)}
.hero-title{left:118px;top:108px;font-size:36px;font-weight:800}
.hero-title .o{color:var(--orange)}.hero-title .g{color:var(--green)}
.hero-sub{left:118px;top:159px;font-size:19px;color:var(--white);font-weight:600}
.hero-text{left:118px;top:196px;width:560px;font-size:12.5px;line-height:1.8;color:#e6e6e6}
.btn{display:inline-flex;align-items:center;gap:8px;font-weight:700;color:var(--white);border-radius:4px}
.hero-btn{left:118px;top:290px;height:44px;padding:0 18px;background:var(--orange);font-size:16px}
.slider-arrow{top:210px;width:52px;height:52px;border-radius:50%;border:2px solid var(--white);background:rgba(0,0,0,.25);display:flex;align-items:center;justify-content:center}
.hero-collage{left:728px;top:88px}

/* welcome */
.welcome{top:637px;height:454px;background:var(--white)}
.section-head{display:flex;align-items:center;gap:10px;font-size:19px;font-weight:700;color:#444}
.head-dot{width:22px;height:22px;border-radius:50%;background:var(--green)}
.welcome .section-head{left:0;width:1200px;top:40px;justify-content:center}
.welcome-intro{left:260px;top:96px;width:680px;text-align:center;font-size:12px;line-height:1.85;color:var(--muted)}
.service{top:160px;width:320px;text-align:center}
.service h3{margin-top:14px;font-size:14px;font-weight:700;color:#444}
.service p{margin-top:12px;font-size:11.5px;line-height:2;color:var(--muted)}

/* products */
.products{top:1091px;height:841px;background:var(--light)}
.products .section-head{left:87px;top:46px;font-size:15px}
.head-rule{left:87px;top:94px;width:742px;height:1px;background:var(--line)}
.head-rule::before{content:"";position:absolute;left:0;top:-1px;width:75px;height:3px;background:var(--orange)}
.pager{top:44px;width:26px;height:26px;border-radius:50%;border:1px solid #bbb;display:flex;align-items:center;justify-content:center}
.card{width:240px;height:330px;background:var(--white);border:1px solid var(--line);text-align:center}
.card-photo{margin:8px;height:190px}
.price{margin-top:18px;font-size:20px;font-weight:700;color:var(--green)}
.card h4{margin-top:10px;font-size:13.5px;font-weight:700;color:#444}
.card-btn{margin-top:12px;height:32px;padding:0 14px;font-size:11px;border-radius:16px;background:linear-gradient(#a9d64a,var(--green-dark))}
.card-btn.cart{background:linear-gradient(#fba13c,var(--orange-dark))}
.categories{left:856px;top:40px;width:257px;height:428px;background:var(--orange)}
.cat-head{height:48px;background:var(--green);color:var(--white);font-size:15px;font-weight:700;padding:0 18px;display:flex;align-items:center;justify-content:space-between}
.cat-list{list-style:none;padding:10px 12px 0 14px}
.cat-list li{height:32.6px;line-height:32.6px;font-size:9.5px;font-weight:600;color:var(--white);border-bottom:1px solid rgba(255,255,255,.18);padding-left:22px;position:relative;text-transform:uppercase;white-space:nowrap;overflow:hidden}
.cat-list li::before{content:"";position:absolute;left:4px;top:14px;width:0;height:0;border-left:5px solid var(--white);border-top:3px solid transparent;border-bottom:3px solid transparent}
.newsletter{left:856px;top:492px;width:257px;height:340px;background:#4a4a4a;text-align:center;padding:26px 18px 0}
.newsletter h3{font-size:19px;font-weight:700;color:var(--white)}
.newsletter p{margin-top:12px;font-size:11px;font-style:italic;line-height:1.8;color:#e6e6e6;white-space:nowrap}
.field{margin-top:14px;height:42px;background:var(--white);border-radius:2px;font-size:11px;font-style:italic;color:#777;text-align:left;padding:0 12px;line-height:42px}
.subscribe{margin-top:14px;height:44px;line-height:44px;background:linear-gradient(#a9d64a,var(--green-dark));color:var(--white);font-weight:700;font-size:15px;border-radius:2px}

/* band */
.band{top:1932px;height:220px;background:linear-gradient(90deg,#84b92f,var(--green) 50%,#86bb31)}
.band h2{left:111px;top:68px;font-size:22px;font-weight:700;color:var(--white)}
.band p{left:111px;top:110px;width:660px;font-size:12.5px;font-style:italic;line-height:1.9;color:#f4faea}
.band-btn{left:816px;top:82px;width:266px;height:60px;border:2px solid var(--white);border-radius:30px;color:var(--white);font-size:13px;display:flex;align-items:center;justify-content:center}

/* package */
.package{top:2152px;height:427px;background:var(--white)}
.package .section-head{left:0;width:1200px;top:40px;justify-content:center;font-size:17px}
.package-photo{left:88px;top:130px;width:440px;height:220px;border-radius:10px;background:linear-gradient(160deg,#4a4a4a,#1f1f1f);transform:skewY(-8deg)}
.pkg-title{left:567px;top:110px;font-size:19px;font-weight:700;color:var(--green)}
.pkg-rule{left:567px;top:92px;width:420px;height:1px;background:var(--line)}
.pkg-rule::before{content:"";position:absolute;left:0;top:-1px;width:48px;height:3px;background:var(--orange)}
.pkg-price{left:567px;top:150px;font-size:17px;font-weight:700;color:var(--orange)}
.pkg-text{left:567px;top:188px;width:500px;font-size:12.5px;line-height:1.9;color:var(--muted)}
.timer{top:305px;width:68px;height:68px;border-radius:50%;border:3px solid #e8e8e8;border-top-color:var(--green);border-right-color:var(--green);text-align:center;padding-top:11px}
.timer b{display:block;font-size:22px;font-weight:700;color:#444;line-height:1}
.timer span{font-size:10px;color:#888}

/* footer */
.site-footer{top:2579px;height:268px;background:var(--footer)}
.foot-brand{left:97px;top:80px;display:flex;align-items:center;gap:14px}
.foot-brand .brand-dot{width:62px;height:62px}
.foot-brand .brand-name{font-size:27px}
.foot-col h4{font-size:17px;font-weight:600;color:var(--white)}
.foot-line{display:flex;align-items:flex-start;gap:12px;font-size:11px;color:#e0e0e0;line-height:1.7}
.foot-line svg{flex:none;margin-top:3px}
.quick{list-style:none;margin-top:18px}
.quick li{height:24px;font-size:11px;color:#e0e0e0;padding-left:28px;position:relative}
.quick li::before{content:"";position:absolute;left:4px;top:5px;border-left:5px solid var(--white);border-top:4px solid transparent;border-bottom:4px solid transparent}
.social{display:flex;gap:8px;margin-top:20px}
.social span{width:34px;height:34px;border-radius:50%;border:2px solid var(--white)}
.copyright{top:2847px;height:66px;background:var(--orange);color:var(--white);font-size:12px;text-align:center;line-height:66px}
</style>
</head>
<body>

<header class="site-header">
  <div class="abs brand"><span class="brand-dot"></span><span class="brand-name">PONDERMESH</span></div>
  <div class="abs contact-chip" style="left:573px">
    <span class="chip-icon"><svg width="22" height="22" viewBox="0 0 24 24"><path fill="#fff" d="M6.6 10.8a15.1 15.1 0 0 0 6.6 6.6l2.2-2.2c.3-.3.7-.4 1-.2 1.1.4 2.3.6 3.6.6.6 0 1 .4 1 1V20c0 .6-.4 1-1 1A17 17 0 0 1 3 4c0-.6.4-1 1-1h3.5c.6 0 1 .4 1 1 0 1.3.2 2.5.6 3.6.1.3 0 .7-.2 1z"/></svg></span>
    <div class="chip-label">CALL US:<b>0141-555-0182</b></div>
  </div>
  <div class="abs contact-chip" style="left:806px">
    <span class="chip-icon"><svg width="22" height="18" viewBox="0 0 22 16"><rect x="0" y="0" width="22" height="16" rx="2" fill="#fff"/><path d="M1 1l10 8 10-8" stroke="#9bcb3c" stroke-width="2" fill="none"/></svg></span>
    <div class="chip-label">EMAIL :<b>sales@pondermeshpaths.co.uk</b></div>
  </div>
</header>

<nav class="main-nav">
  <a class="abs nav-item active">HOME</a>
  <a class="abs nav-item" style="left:224px">SHOP</a>
  <a class="abs nav-item" style="left:320px">ABOUT US</a>
  <a class="abs nav-item" style="left:448px">GROUND SOLUTIONS</a>
  <a class="abs nav-item" style="left:640px">PONDERMESH</a>
  <a class="abs nav-item" style="left:790px">CONTACT US</a>
  <div class="abs search">Search<svg width="14" height="14" viewBox="0 0 14 14"><circle cx="6" cy="6" r="4.5" stroke="#555" stroke-width="2" fill="none"/><path d="M9.5 9.5L13 13" stroke="#555" stroke-width="2"/></svg></div>
</nav>

<section class="hero" role="img" aria-label="Background photo of a gravel driveway laid on reinforcement grid">
  <div class="abs hero-title"><span class="o">PONDERMESH</span> <span class="g">DRIVEWAYS</span></div>
  <div class="abs hero-sub">AFFORDABLE AND GREEN SOLUTIONS FOR FLOOD PREVENTION</div>
  <p class="abs hero-text">Pondermesh is a family run company that specialises in stabilisation grid systems for gravel and grass surfaces. Our main focus is to provide Quality products at an affordable price and which meets the techniques which is Sustainable Urban Drainage Systems.</p>
  <a class="abs btn hero-btn">SHOP NOW <svg width="16" height="16" viewBox="0 0 16 16"><circle cx="8" cy="8" r="7" stroke="#fff" stroke-width="1.6" fill="none"/><path d="M6.5 5l3 3-3 3" stroke="#fff" stroke-width="1.6" fill="none"/></svg></a>
  <div class="abs slider-arrow" style="left:26px"><svg width="14" height="18" viewBox="0 0 14 18"><path d="M10 2L3 9l7 7" stroke="#fff" stroke-width="3" fill="none"/></svg></div>
  <div class="abs slider-arrow" style="left:1122px"><svg width="14" height="18" viewBox="0 0 14 18"><path d="M4 2l7 7-7 7" stroke="#fff" stroke-width="3" fill="none"/></svg></div>
  <svg class="abs hero-collage" width="390" height="330" viewBox="0 0 390 330" role="img" aria-label="Hexagon collage of photos showing gravel grids being installed">
    <g stroke="#fff" stroke-width="3">
      <polygon points="55,0 110,30 110,90 55,120 0,90 0,30" fill="#9c9c9c"/>
      <polygon points="187,0 242,30 242,90 187,120 132,90 132,30" fill="#6f6f6a"/>
      <polygon points="319,0 374,30 374,90 319,120 264,90 264,30" fill="#7c9a4e"/>
      <polygon points="121,110 176,140 176,200 121,230 66,200 66,140" fill="#a79b72"/>
      <polygon points="253,110 308,140 308,200 253,230 198,200 198,140" fill="#8a8a86"/>
      <polygon points="187,210 242,240 242,300 187,330 132,300 132,240" fill="#8da36a"/>
    </g>
  </svg>
</section>

<section class="welcome">
  <div class="abs section-head"><span class="head-dot"></span>WELCOME TO PONDER MESH</div>
  <p class="abs welcome-intro">Pondermesh is a family run company that specialises in stabilisation grid systems for gravel and grass surfaces. Our main focus is to incorporate the SUDS techniques which is Sustainable Urban Drainage Systems.</p>

  <div class="abs service" style="left:92px">
    <svg width="136" height="150" viewBox="0 0 136 150"><polygon points="68,2 132,38 132,112 68,148 4,112 4,38" fill="none" stroke="#f78f20" stroke-width="3"/><polygon points="68,12 124,43 124,107 68,138 12,107 12,43" fill="#f78f20"/><circle cx="68" cy="68" r="18" fill="none" stroke="#fff" stroke-width="4"/><rect x="60" y="86" width="16" height="14" fill="#fff"/><path d="M68 36v-8M44 46l-6-6M92 46l6-6M36 68h-8M100 68h8" stroke="#fff" stroke-width="4"/></svg>
    <h3>GROUND SOLUTIONS</h3>
    <p>Pondermesh is a family run company that specialises in stabilisation grid systems for gravel and grass which is Sustainable Urban Drainage Systems.</p>
  </div>
  <div class="abs service" style="left:438px">
    <svg width="136" height="150" viewBox="0 0 136 150"><polygon points="68,2 132,38 132,112 68,148 4,112 4,38" fill="none" stroke="#9bcb3c" stroke-width="3"/><polygon points="68,12 124,43 124,107 68,138 12,107 12,43" fill="#9bcb3c"/><g fill="none" stroke="#fff" stroke-width="4"><rect x="44" y="51" width="48" height="48"/><path d="M60 51v48M76 51v48M44 67h48M44 83h48"/></g></svg>
    <h3>PONDERMESH</h3>
    <p>Pondermesh is a family run company that specialises in stabilisation grid systems for gravel and grass which is Sustainable Urban Drainage Systems.</p>
  </div>
  <div class="abs service" style="left:786px">
    <svg width="136" height="150" viewBox="0 0 136 150"><polygon points="68,2 132,38 132,112 68,148 4,112 4,38" fill="none" stroke="#f78f20" stroke-width="3"/><polygon points="68,12 124,43 124,107 68,138 12,107 12,43" fill="#f78f20"/><path d="M50 98C42 72 60 50 90 46c2 30-12 52-40 52z" fill="none" stroke="#fff" stroke-width="4"/><path d="M50 98l28-34" stroke="#fff" stroke-width="4"/></svg>
    <h3>ECO SERVICES</h3>
    <p>Pondermesh is a family run company that specialises in stabilisation grid systems for gravel and grass which is Sustainable Urban Drainage Systems.</p>
  </div>
</section>

<section class="products">
  <div class="abs section-head"><span class="head-dot"></span>FEATURED PRODUCTS</div>
  <div class="abs head-rule"></div>
  <span class="abs pager" style="left:768px"><svg width="8" height="10" viewBox="0 0 8 10"><path d="M6 1L2 5l4 4" stroke="#888" stroke-width="1.6" fill="none"/></svg></span>
  <span class="abs pager" style="left:798px"><svg width="8" height="10" viewBox="0 0 8 10"><path d="M2 1l4 4-4 4" stroke="#888" stroke-width="1.6" fill="none"/></svg></span>

  <div class="abs card" style="left:87px;top:123px"><div class="card-photo" role="img" aria-label="Photo of geotextile membrane laid on a site" style="background:linear-gradient(#8a8a7e,#5d5d58)"></div><div class="price">£ 44.99</div><h4>GEOTEXTILE MEMBRANES</h4><a class="btn card-btn cart">ADD TO CART ⊕</a></div>
  <div class="abs card" style="left:338px;top:123px"><div class="card-photo" role="img" aria-label="Photo of a light domestic gravel driveway" style="background:linear-gradient(#b8ab8e,#8f8470)"></div><div class="price">£ 44.99</div><h4>LIGHT DOMESTIC DRIVEWAYS</h4><a class="btn card-btn">VIEW MORE ⊕</a></div>
  <div class="abs card" style="left:589px;top:123px"><div class="card-photo" role="img" aria-label="Photo of heavy domestic driveway grid installation" style="background:linear-gradient(#6d7f5a,#4f5a44)"></div><div class="price">£ 44.99</div><h4>HEAVY DOMESTIC DRIVEWAYS</h4><a class="btn card-btn">VIEW MORE ⊕</a></div>
  <div class="abs card" style="left:87px;top:472px"><div class="card-photo" role="img" aria-label="Photo of commercial parking grid being laid" style="background:linear-gradient(#8d8a83,#5e5a55)"></div><div class="price">£ 44.99</div><h4>COMMERCIAL PARKING</h4><a class="btn card-btn">VIEW MORE ⊕</a></div>
  <div class="abs card" style="left:338px;top:472px"><div class="card-photo" role="img" aria-label="Photo of gravel filled parking and pathway grid" style="background:linear-gradient(#a08868,#c4a36d)"></div><div class="price">£ 44.99</div><h4>PARKING AND PATHWAY</h4><a class="btn card-btn">VIEW MORE ⊕</a></div>
  <div class="abs card" style="left:589px;top:472px"><div class="card-photo" role="img" aria-label="Photo of black equestrian grid panels in a field" style="background:linear-gradient(#7a9a86,#2e3230)"></div><div class="price">£ 44.99</div><h4>STABLEGUARD GRID</h4><a class="btn card-btn">VIEW MORE ⊕</a></div>

  <aside class="abs categories">
    <div class="cat-head">PRODUCTS CATEGORIES <svg width="16" height="12" viewBox="0 0 16 12"><path d="M0 1h16M0 6h16M0 11h16" stroke="#fff" stroke-width="2"/></svg></div>
    <ul class="cat-list">
      <li>Geotextile Membranes</li><li>Light Domestic Driveways</li><li>Heavy Domestic Driveways</li><li>Parking and Pathway System</li><li>Grass Reinforcement Mesh &amp; Turf</li><li>Reinforcement Mesh</li><li>Steel U Pins</li><li>Commercial Parking System</li><li>Stableguard Grid</li><li>Monthly Specials</li><li>Garden Edging</li>
    </ul>
  </aside>
  <aside class="abs newsletter">
    <h3>NEWSLETTER</h3>
    <p>Pondermesh is a family run company tradi-<br>tional of a gravel driveway</p>
    <div class="field">Enter Your Email :</div>
    <div class="field">Enter Your Password :</div>
    <div class="subscribe">SUBSCRIBE</div>
  </aside>
</section>

<section class="band" role="img" aria-label="Green banner with a faint photo of a gravel grid">
  <h2 class="abs">CONTAINED GRAVEL FOR PARKING &amp; PATHWAYS</h2>
  <p class="abs">Pondermesh is a family run company that specialises in stabilisation grid systems for gravel and grass our main focus is apply a perme that keeps the traditional look of a gravel driveway.</p>
  <a class="abs band-btn">CLICK HERE FOR MORE INFO</a>
</section>

<section class="package">
  <div class="abs section-head"><span class="head-dot"></span>FEATURED PACKAGE</div>
  <div class="abs package-photo" role="img" aria-label="Product photo of a black plastic gravel grid panel"></div>
  <div class="abs pkg-rule"></div>
  <h3 class="abs pkg-title">PONDERMESH ECO SOLUTIONS LTD</h3>
  <div class="abs pkg-price">Now only $ 50.00</div>
  <p class="abs pkg-text">Pondermesh is a family run company that specialises in stabilisation grid systems for gravel and grass surfaces. Our main focus is to provide Quality products at an afford able price and which meets the requirements of our customers.We supply a perme that keeps the traditional look of a gravel driveway</p>
  <div class="abs timer" style="left:569px"><b>24</b><span>days</span></div>
  <div class="abs timer" style="left:647px"><b>15</b><span>hours</span></div>
  <div class="abs timer" style="left:724px"><b>20</b><span>mins</span></div>
  <div class="abs timer" style="left:802px"><b>40</b><span>secs</span></div>
</section>

<footer class="site-footer">
  <div class="abs foot-brand"><span class="brand-dot"></span><span class="brand-name">PONDERMESH</span></div>
  <div class="abs foot-col" style="left:435px;top:56px;width:240px">
    <h4>Contact Us</h4>
    <div class="foot-line" style="margin-top:28px"><svg width="12" height="12" viewBox="0 0 24 24"><path fill="#fff" d="M6.6 10.8a15.1 15.1 0 0 0 6.6 6.6l2.2-2.2c.3-.3.7-.4 1-.2 1.1.4 2.3.6 3.6.6.6 0 1 .4 1 1V20c0 .6-.4 1-1 1A17 17 0 0 1 3 4c0-.6.4-1 1-1h3.5c.6 0 1 .4 1 1 0 1.3.2 2.5.6 3.6.1.3 0 .7-.2 1z"/></svg>0141-555-0182 (Phone)</div>
    <div class="foot-line" style="margin-top:10px"><svg width="12" height="12" viewBox="0 0 12 12"><rect x="1" y="4" width="10" height="6" fill="#fff"/><rect x="3" y="1" width="6" height="3" fill="#fff"/></svg>0845-555-0745 (Fax)</div>
    <div class="foot-line" style="margin-top:10px"><svg width="12" height="10" viewBox="0 0 12 10"><rect width="12" height="10" rx="1" fill="#fff"/><path d="M1 1l5 4 5-4" stroke="#3a3a3a" fill="none"/></svg>sales@pondermeshpaths.co.uk</div>
    <div class="foot-line" style="margin-top:10px"><svg width="12" height="14" viewBox="0 0 12 14"><path d="M6 0a5 5 0 0 1 5 5c0 4-5 9-5 9S1 9 1 5a5 5 0 0 1 5-5z" fill="#fff"/><circle cx="6" cy="5" r="2" fill="#3a3a3a"/></svg>Meadowbank House, Riverside Ind<br>Est, Glenhaven, G99 9ZZ</div>
  </div>
  <div class="abs foot-col" style="left:713px;top:56px">
    <h4>Quick Links</h4>
    <ul class="quick"><li>HOME</li><li>SHOP</li><li>ABOUT US</li><li>GROUND SOLUTIONS</li><li>PONDERMESH</li><li>CONTACT US</li></ul>
  </div>
  <div class="abs foot-col" style="left:901px;top:56px;width:220px">
    <h4>Follow Us</h4>
    <p class="foot-line" style="margin-top:18px">Pondermesh is a family run company that specialises in stabilisation grid and grass surfaces.</p>
    <div class="social"><span></span><span></span><span></span><span></span><span></span></div>
  </div>
</footer>

<div class="abs copyright" style="left:0;width:1200px">© Copyright 2016 Pondermesh Paths.All Rights Reserved</div>

</body>
</html>
```